Consumer and commercial IOT solutions (Internet Of Things)

We are a startup and are looking for business cards with logo. The logo will appear on all of our media as well as our ecommerce site and social sites that have yet to be developed. We want to present a fresh face on a high tech company that innovates at every turn. You can read about our solutions on our information only web site www.plonaxhub.net - We have some wording we would like used on our business cards but there is no place for this except for here. The company name is "RM Industrial IOT" I have some samples of logos I am interested in seeing but I will let your team make the initial presentations

```html
<!DOCTYPE html>
<html lang="en">
<head>
<meta charset="utf-8">
<title>RM Industrial IOT – Business Card</title>
<link rel="stylesheet" href="https://fonts.googleapis.com/css2?family=Arimo:wght@400;700&display=swap">
<style>
  :root {
    --navy: #0b3f6a;
    --orange: #f7941d;
    --white: #ffffff;
    --foil-light: #f4f2f2;
    --foil-mid: #d9d4d4;
    --foil-dark: #b9b3b3;
    --backdrop: #e9e7e5;
  }
  * { margin: 0; padding: 0; box-sizing: border-box; }
  html, body {
    width: 1200px;
    height: 900px;
    overflow: hidden;
    background: var(--backdrop);
    font-family: "Arimo", Arial, sans-serif;
  }
  .business-card {
    position: absolute;
    left: 100px;
    top: 141px;
    width: 1000px;
    height: 618px;
    background: var(--navy);
    overflow: hidden;
    box-shadow: 0 10px 30px rgba(0, 0, 0, 0.18);
  }
  .accent-band {
    position: absolute;
    left: 715px;
    top: 0;
    width: 285px;
    height: 100%;
    background: var(--orange);
  }
  .brand-disc {
    position: absolute;
    left: 462px;
    top: 56px;
    width: 504px;
    height: 504px;
    border-radius: 50%;
    background: radial-gradient(circle at 40% 35%, var(--foil-light) 0%, var(--foil-mid) 60%, var(--foil-dark) 100%);
  }
  .company-name {
    position: absolute;
    left: 46px;
    top: 102px;
    color: var(--white);
    font-size: 34px;
    font-weight: 400;
    line-height: 40px;
    white-space: nowrap;
  }
  .person-name {
    position: absolute;
    left: 46px;
    top: 252px;
    color: var(--orange);
    font-size: 41px;
    font-weight: 700;
    letter-spacing: 0.5px;
  }
  .person-title {
    position: absolute;
    left: 45px;
    top: 295px;
    color: var(--white);
    font-size: 28px;
  }
  .contact-list {
    position: absolute;
    left: 45px;
    top: 358px;
    list-style: none;
    color: var(--white);
    font-size: 28px;
  }
  .contact-item {
    display: flex;
    align-items: center;
    height: 36.5px;
  }
  .contact-icon {
    width: 26px;
    height: 26px;
    margin-right: 9px;
    flex: none;
  }
  .address {
    position: absolute;
    left: 46px;
    top: 487px;
    color: var(--white);
    font-size: 28px;
    line-height: 36px;
    font-style: normal;
  }
</style>
</head>
<body>
  <section class="business-card">
    <div class="accent-band"></div>
    <div class="brand-disc"></div>

    <div class="company-name">RM Industrial IoT</div>

    <h1 class="person-name">DANIEL MORROW</h1>
    <p class="person-title">Managing Director</p>

    <ul class="contact-list">
      <li class="contact-item">
        <svg class="contact-icon" viewBox="0 0 24 24" aria-hidden="true">
          <path fill="var(--orange)" d="M6.6 10.8c1.4 2.8 3.8 5.1 6.6 6.6l2.2-2.2c.3-.3.7-.4 1-.2 1.1.4 2.3.6 3.6.6.6 0 1 .4 1 1V20c0 .6-.4 1-1 1C10.6 21 3 13.4 3 4c0-.6.4-1 1-1h3.5c.6 0 1 .4 1 1 0 1.3.2 2.5.6 3.6.1.3 0 .7-.2 1L6.6 10.8z"/>
        </svg>
        <span>044-987 210 364</span>
      </li>
      <li class="contact-item">
        <svg class="contact-icon" viewBox="0 0 24 24" aria-hidden="true">
          <rect x="2" y="5" width="20" height="14" fill="var(--orange)"/>
          <path d="M2 5l10 8 10-8" fill="none" stroke="var(--navy)" stroke-width="1.6"/>
        </svg>
        <span>hello@plonaxhub.net</span>
      </li>
      <li class="contact-item">
        <svg class="contact-icon" viewBox="0 0 24 24" aria-hidden="true">
          <g fill="none" stroke="var(--orange)" stroke-width="1.8">
            <circle cx="12" cy="12" r="9.5"/>
            <ellipse cx="12" cy="12" rx="4.5" ry="9.5"/>
            <line x1="2.5" y1="12" x2="21.5" y2="12"/>
            <line x1="4" y1="7.5" x2="20" y2="7.5"/>
            <line x1="4" y1="16.5" x2="20" y2="16.5"/>
          </g>
        </svg>
        <span>www.plonaxhub.net</span>
      </li>
    </ul>

    <address class="address">421, Address line goes here<br>45452,Country Name</address>
  </section>
</body>
</html>
```